Prosperity Pathway Basics PowerPoint

Please edit the following attached PowerPoint entitled workshop. Use the other attached PDF "TerraVesta Northern California Value Proposition" as a reference for the design and color I would like.

```html
<!DOCTYPE html>
<html lang="en">
<head>
<meta charset="utf-8">
<title>Prosperity Pathway Basics — Workshop Slides</title>
<link rel="stylesheet" href="https://fonts.googleapis.com/css2?family=Lexend:wght@400;500;600&family=Lato:wght@400;700&display=swap">
<style>
:root{
  --navy:#0a2c70;
  --sky:#9dd3ee;
  --mid:#2a78c0;
  --page:#eef4fb;
  --ink:#1b1b1b;
  --white:#ffffff;
}
*{box-sizing:border-box;margin:0;padding:0}
html,body{width:1023px;height:1200px;overflow:hidden;background:var(--page)}
body{position:relative;font-family:'Lato',sans-serif;color:var(--ink)}
.slide{position:absolute;width:472px;height:266px;background:var(--white);overflow:hidden;box-shadow:0 2px 10px rgba(10,44,112,.10)}
.col-left{left:27px}.col-right{left:522px}
.row-1{top:27px}.row-2{top:314px}.row-3{top:605px}.row-4{top:896px}
.abs{position:absolute}
.heading{font-family:'Lexend',sans-serif;font-weight:500;color:var(--navy);font-size:12.5px;position:absolute;white-space:nowrap}
.rule{position:absolute;height:1.2px;background:var(--navy)}
.rule::after{content:"";position:absolute;top:-2px;width:5px;height:5px;border-radius:50%;background:var(--navy)}
.rule.dot-right::after{right:-2px}.rule.dot-left::after{left:-2px}
.footer-band{position:absolute;left:0;right:0;top:244px;height:14px;background:var(--navy)}
.footer-logo{position:absolute;top:240px;left:24px;width:81px;height:22px;background:var(--white);display:flex;align-items:center;justify-content:center;gap:3px}
.brand{font-family:'Lexend',sans-serif;font-weight:500;color:var(--navy);font-size:10px;line-height:1}
.brand-mark{width:4px;height:4px;border-radius:50%;background:var(--navy)}
.page-no{position:absolute;top:248px;right:24px;font-family:'Lexend',sans-serif;font-weight:600;font-size:5px;color:var(--white);letter-spacing:.2px}
.photo{position:absolute}
/* slide 1 */
.cover-text{position:absolute;left:22px;top:74px;font-family:'Lexend',sans-serif;font-size:9px;line-height:21px;font-weight:500}
.cover-text .accent{color:var(--navy);font-weight:600}
/* slide 2 */
.frame{position:absolute;top:72px;width:136px;height:105px;border-radius:7px;border:3px solid}
.icon-badge{position:absolute;width:40px;height:40px;border-radius:50%;display:flex;align-items:center;justify-content:center}
.vs{position:absolute;left:224px;top:116px;font-family:'Lexend',sans-serif;font-weight:600;font-size:16px;color:var(--navy)}
.card-label{position:absolute;top:186px;width:140px;text-align:center;font-family:'Lexend',sans-serif;font-weight:500;font-size:8px}
.card-sub{position:absolute;top:204px;width:140px;text-align:center;font-family:'Lexend',sans-serif;font-weight:500;font-size:5px;letter-spacing:.3px}
/* slide 3 */
.loss-copy{position:absolute;right:24px;top:57px;text-align:right;font-size:6.6px;line-height:14.8px;width:260px}
.loss-list{position:absolute;right:24px;top:122px;list-style:none;text-align:right;font-size:6.6px;line-height:17.8px}
.loss-list li::after{content:"";display:inline-block;width:3px;height:3px;border:1px solid var(--navy);border-radius:50%;margin-left:5px;vertical-align:middle;box-shadow:inset 0 0 0 1px var(--white);background:var(--navy)}
/* slide 4 */
.efficiency-copy{position:absolute;left:24px;top:70px;width:215px;font-size:8px;line-height:17.8px}
.efficiency-copy p+p{margin-top:18px}
/* slide 5 */
.legend{position:absolute;top:29px;font-family:'Lexend',sans-serif;font-weight:500;font-size:7.5px;color:var(--ink);display:flex;align-items:center;gap:6px}
.legend::before{content:"";width:3px;height:3px;border-radius:50%;border:1px solid var(--navy);box-shadow:inset 0 0 0 1px var(--white);background:var(--navy)}
.disc{position:absolute;width:51px;height:51px;border-radius:50%;background:var(--navy);color:var(--white);font-family:'Lexend',sans-serif;font-weight:500;font-size:8px;line-height:12.5px;display:flex;align-items:center;justify-content:center;text-align:center}
.vbar{position:absolute;background:var(--sky);color:var(--navy);font-family:'Lexend',sans-serif;font-weight:500;font-size:9px;letter-spacing:4px;writing-mode:vertical-rl;transform:rotate(180deg);display:flex;align-items:center;justify-content:center}
/* slide 6 */
.bubble{position:absolute;width:124px;height:124px;border-radius:50%;display:flex;flex-direction:column;align-items:center;justify-content:center;text-align:center;padding:0 10px}
.badge{position:absolute;width:34px;height:34px;border-radius:50%;border:2px solid var(--white);display:flex;align-items:center;justify-content:center;font-family:'Lexend',sans-serif;font-weight:600;font-size:14px}
.q-text{font-family:'Lexend',sans-serif;font-weight:500;font-size:5.5px;line-height:11.5px;color:var(--ink)}
.a-title{font-family:'Lexend',sans-serif;font-weight:500;font-size:5.6px;line-height:8px;color:var(--white);margin-bottom:3px}
.a-body{font-size:3.8px;line-height:8.6px;color:var(--white)}
/* slide 7 */
.objective-copy{position:absolute;left:23px;top:58px;width:430px;font-size:7px;line-height:13.5px}
.phase-label{position:absolute;font-family:'Lato',sans-serif;font-size:6.5px;color:var(--ink);white-space:nowrap}
/* slide 8 */
.transfer-copy{position:absolute;left:229px;top:56px;width:220px;font-size:6.6px;line-height:14.8px;text-align:justify;text-align-last:right}
.transfer-copy p+p{margin-top:14.8px}
</style>
</head>
<body>

<!-- Slide 1: Objective -->
<section class="slide col-left row-1">
  <div class="abs" style="left:325px;top:0;width:147px;height:266px;background:var(--navy)"></div>
  <div class="abs" style="left:211px;top:15px;width:236px;height:236px;border-radius:50%;background:var(--white)"></div>
  <div class="photo" role="img" aria-label="Climber planting a red flag on a snowy mountain summit above the clouds" style="left:231px;top:35px;width:196px;height:196px;border-radius:50%;background:radial-gradient(circle at 50% 30%,#d9ecf6 0%,#8fbdd8 45%,#3d5f80 75%,#1f3550 100%)"></div>
  <div class="abs" style="left:22px;top:32px;display:flex;align-items:center;gap:3px"><span class="brand-mark"></span><span class="brand" style="font-size:13px">TerraVesta</span></div>
  <div class="cover-text">
    <div class="accent">Objective:</div>
    <div>• Build as big as possible</div>
    <div class="accent">How:</div>
    <div>Higher rates of return?</div>
    <div>• More risk?</div>
    <div>• "Better" products?</div>
    <div class="accent">Having an efficient overall strategy</div>
    <div class="accent">is the key; it all starts here!</div>
  </div>
</section>

<!-- Slide 2: Your Money -->
<section class="slide col-right row-1">
  <h2 class="heading" style="left:23px;top:20px">Your Money</h2>
  <div class="rule dot-right" style="left:0;top:43px;width:64px"></div>
  <div class="frame" style="left:54px;border-color:var(--sky)">
    <div class="photo" role="img" aria-label="Workshop bench full of hand tools and power tools" style="inset:2px;border-radius:4px;background:linear-gradient(160deg,#7a5a3a,#c8902f 45%,#3b3a3a 80%,#b92a2a)"></div>
  </div>
  <div class="frame" style="left:283px;border-color:var(--navy)">
    <div class="photo" role="img" aria-label="Mountaineer with backpack climbing a snowy ridge" style="inset:2px;border-radius:4px;background:linear-gradient(170deg,#c7d8e6,#8aa6bf 45%,#e9eef3 75%,#5d738a)"></div>
  </div>
  <div class="icon-badge" style="left:169px;top:104px;background:var(--sky)">
    <svg width="22" height="22" viewBox="0 0 24 24" fill="none" stroke="#0a2c70" stroke-width="1.3"><circle cx="9" cy="7" r="3"/><circle cx="16" cy="8" r="2.4"/><path d="M3 19h5l5-2h5l2-2-2-1-5 1"/><path d="M3 15h3l4 2"/></svg>
  </div>
  <div class="vs">VS</div>
  <div class="icon-badge" style="left:265px;top:104px;background:var(--navy)">
    <svg width="22" height="22" viewBox="0 0 24 24" fill="none" stroke="#ffffff" stroke-width="1.3"><path d="M12 5a5 5 0 0 0-3 9v2h6v-2a5 5 0 0 0-3-9z"/><path d="M10 19h4M12 1v2M4 9H2M22 9h-2M5 3l1.5 1.5M19 3l-1.5 1.5"/></svg>
  </div>
  <div class="card-label" style="left:53px">Equipment and Tools</div>
  <div class="card-sub" style="left:53px;color:var(--sky)">PRODUCTS</div>
  <div class="card-label" style="left:279px">Skill and Technique</div>
  <div class="card-sub" style="left:279px;color:var(--navy)">STRATEGY</div>
  <div class="footer-band"></div>
  <div class="footer-logo"><span class="brand-mark"></span><span class="brand">TerraVesta</span></div>
  <div class="page-no">PAGE NO: 02</div>
</section>

<!-- Slide 3: Why is Your Strategy so Important -->
<section class="slide col-left row-2">
  <div class="abs" style="left:40px;top:30px;width:160px;height:200px;border-radius:50%;background:radial-gradient(circle,rgba(157,211,238,.35),rgba(157,211,238,0) 70%)"></div>
  <div class="photo" role="img" aria-label="Two colleagues smiling while reviewing a laptop together" style="left:24px;top:23px;width:89px;height:121px;border-radius:6px;background:linear-gradient(135deg,#4a4540,#8a7868 50%,#2f3a48)"></div>
  <div class="photo" role="img" aria-label="Hand drawing a rising financial chart on a glowing screen" style="left:129px;top:97px;width:89px;height:120px;border-radius:6px;background:linear-gradient(160deg,#1d3a5a,#2f6c8c 50%,#0e1e30)"></div>
  <h2 class="heading" style="right:24px;top:20px">Why is Your Strategy so Important?</h2>
  <div class="rule dot-left" style="left:410px;top:45px;width:62px"></div>
  <div class="loss-copy">
    We all only have a finite amount of money...we have to be efficient with<br>
    it in the short time we have.<br>
    Inefficiencies cause major losses to occur.<br>
    <b>These losses can be reflected in:</b>
  </div>
  <ul class="loss-list">
    <li>Lower Current Lifestyle</li>
    <li>Lower Retirement Income Inadequate Protection</li>
    <li>Loss Of Financial Control</li>
    <li>Financial Vulnerability</li>
    <li>Higher Taxes And Fees</li>
    <li>Less Benefits</li>
  </ul>
  <div class="footer-band"></div>
  <div class="footer-logo"><span class="brand-mark"></span><span class="brand">TerraVesta</span></div>
  <div class="page-no">PAGE NO: 03</div>
</section>

<!-- Slide 4: How Significant is Efficiency -->
<section class="slide col-right row-2">
  <svg class="abs" style="left:0;top:0" width="472" height="266" aria-hidden="true">
    <circle cx="556" cy="137" r="290" fill="none" stroke="#9dd3ee" stroke-width="2"/>
  </svg>
  <div class="photo" role="img" aria-label="Hand on a keyboard overlaid with glowing hexagon business icons" style="left:276px;top:-143px;width:560px;height:560px;border-radius:50%;background:linear-gradient(100deg,#c98a7a 0%,#5d86c2 18%,#2f5fae 45%,#1b3f84 80%)"></div>
  <h2 class="heading" style="left:23px;top:20px">How Significant is Efficiency?</h2>
  <div class="rule dot-right" style="left:0;top:43px;width:64px"></div>
  <div class="efficiency-copy">
    <p>An individual might be able to create $75,000/year (1 unit) of retirement income based on current savings with an inefficient process.</p>
    <p>The same individual could create $125,000/year of retirement income with an efficient process using the same amount of savings.</p>
  </div>
  <div class="footer-band"></div>
  <div class="footer-logo"><span class="brand-mark"></span><span class="brand">TerraVesta</span></div>
  <div class="page-no">PAGE NO: 04</div>
</section>

<!-- Slide 5: Foundations Framework -->
<section class="slide col-left row-3">
  <h2 class="heading" style="left:23px;top:20px">Foundations Framework<sup style="font-size:6px">TM</sup></h2>
  <div class="rule dot-right" style="left:0;top:43px;width:64px"></div>
  <div class="legend" style="left:228px">Protection (Your Safety Shield)</div>
  <div class="legend" style="left:375px">Wealth Building</div>
  <div class="disc" style="left:55px;top:65px">Protection</div>
  <div class="disc" style="left:113px;top:120px">Protection</div>
  <div class="disc" style="left:55px;top:175px">Protection</div>
  <div class="vbar" style="left:204px;top:66px;width:21px;height:159px">ANNUAL SAVINGS</div>
  <svg class="abs" style="left:0;top:0" width="472" height="266" aria-hidden="true" fill="none" stroke="#7f9cc4" stroke-width=".8">
    <path d="M225 141H249M249 87V212M249 87H265M249 141H365M249 212H365"/>
  </svg>
  <div class="disc" style="left:265px;top:65px">Wealth<br>Building</div>
  <div class="vbar" style="left:322px;top:66px;width:20px;height:49px">SHORT</div>
  <div class="disc" style="left:365px;top:116px">Wealth<br>Building</div>
  <div class="disc" style="left:365px;top:175px">Wealth<br>Building</div>
  <div class="vbar" style="left:427px;top:113px;width:21px;height:112px">LONG TERM</div>
  <div class="footer-band"></div>
  <div class="footer-logo"><span class="brand-mark"></span><span class="brand">TerraVesta</span></div>
  <div class="page-no">PAGE NO: 05</div>
</section>

<!-- Slide 6: Questions & Answers -->
<section class="slide col-right row-3">
  <h2 class="heading" style="left:23px;top:20px">Questions &amp; Answers</h2>
  <div class="rule dot-right" style="left:0;top:43px;width:64px"></div>
  <div class="bubble" style="left:54px;top:80px;background:var(--sky)">
    <p class="q-text">What is the underlying premise<br>for all long term savings<br>anybody does?</p>
    <p class="q-text" style="margin-top:10px">Why are you giving up current<br>enjoyment of your income?</p>
  </div>
  <div class="badge" style="left:99px;top:67px;background:var(--sky);color:var(--navy)">Q</div>
  <div class="abs" style="left:202px;top:128px;display:flex;align-items:center;gap:3px"><span class="brand-mark"></span><span class="brand">TerraVesta</span></div>
  <div class="bubble" style="left:295px;top:80px;background:var(--navy)">
    <p class="a-title">TO HAVE AN INCOME STREAM IN RETIREMENT</p>
    <p class="a-body">It only makes sense then to understand how retirement income streams work so that we can direct the savings we are doing today in ways that gives us the highest income when we retire.</p>
    <p class="a-body" style="margin-top:6px">In other words, how retirement income streams work economically define how to allocate savings today.</p>
  </div>
  <div class="badge" style="left:340px;top:67px;background:var(--navy);color:var(--white)">A</div>
  <div class="footer-band"></div>
  <div class="footer-logo"><span class="brand-mark"></span><span class="brand">TerraVesta</span></div>
  <div class="page-no">PAGE NO: 06</div>
</section>

<!-- Slide 7: What is the objective -->
<section class="slide col-left row-4">
  <div class="photo" role="img" aria-label="Snow-covered mountain peak with a small red flag at the summit under a pale sky" style="left:0;top:98px;width:472px;height:168px;background:linear-gradient(180deg,#ffffff 0%,#dce7ef 30%,#c3d3df 60%,#9fb3c4 100%)"></div>
  <h2 class="heading" style="left:23px;top:20px">What is the objective?</h2>
  <div class="rule dot-right" style="left:0;top:43px;width:64px"></div>
  <p class="objective-copy">This is one continuous journey. There are 2 rates that make up everyone's Retirement Income (both are equally important): 1) Accumulation Rate 2) Distribution Rate.&nbsp;&nbsp;&nbsp; Understanding how retirement income streams work (distribution) defines how to pack your bag in Pre-Retirement. Begin with the end in mind.</p>
  <div class="phase-label" style="left:135px;top:160px;transform:rotate(-56deg)">Pre-Retirement (Accumulation)</div>
  <div class="phase-label" style="left:270px;top:162px;transform:rotate(64deg)">Retirement (Distribution)</div>
  <div class="footer-band"></div>
  <div class="footer-logo"><span class="brand-mark"></span><span class="brand">TerraVesta</span></div>
  <div class="page-no">PAGE NO: 07</div>
</section>

<!-- Slide 8: Dual Strength Approach -->
<section class="slide col-right row-4">
  <svg class="abs" style="left:0;top:0" width="472" height="266" aria-hidden="true">
    <circle cx="10" cy="133" r="197" fill="none" stroke="#9dd3ee" stroke-width="2"/>
  </svg>
  <div class="photo" role="img" aria-label="Business handshake in front of a glowing world map and city skyline" style="left:-178px;top:-50px;width:376px;height:366px;border-radius:50%;background:radial-gradient(circle at 75% 55%,#6b4a32 0%,#a56a35 35%,#d9a15c 60%,#5c4a3c 100%)"></div>
  <h2 class="heading" style="right:23px;top:20px">Dual Strength<sup style="font-size:6px">TM</sup> Approach</h2>
  <div class="rule dot-left" style="left:207px;top:45px;width:265px"></div>
  <div class="transfer-copy">
    <p>There is a major transfer of risk/responsibility from the employer to the employee when you have a Defined Contribution Plan versus a Defined Benefit Plan. Very little education has been given to individuals regarding what they must now do to provide for themselves.</p>
    <p>Equally important is that not only was there a transfer of risk/responsibility that occurred, but in a Defined Contribution Plan the employee is no longer getting both economic powers by default... they are getting the Interest Rates/Rates of Return power, but they must now seek out and understand how to incorporate the Actuarial Science power as they are not getting it by default.</p>
  </div>
  <div class="footer-band"></div>
  <div class="footer-logo"><span class="brand-mark"></span><span class="brand">TerraVesta</span></div>
  <div class="page-no">PAGE NO: 08</div>
</section>

</body>
</html>
```